Business card design needed

Family General Practitioner/ Family Physician.
Logo is the logo of the Noble Guild of Family Healers Oceania
http://kpltw.varendo.example/ImageShelf/marks/pages/NGFHO%20mark_jpg.htm
Updates

Project Deadline Extended
Reason: Just a bit more time to make changes and the weekend for me to look at things closely and to choose. Thanks, Orin

Thanks for all the submissions. So many of them are really works of art. Not one of them are not good. The ones that I am eliminating are the ones that I think are not suitable for me personally only, and because if I don't, it makes it very difficult to decide as many of you are also sending me slight variations of a card. I have just decided to choose a second place card too. Can't thank you all enough. Good luck, Orin. P.S - Working today till 10 pm as the card says :-), so probably won't be able to give a feedback till late Saturday night or Sunday morning here in Sydney, Australia. 

Project Deadline Extended
Reason: Just added a second place to the budget and realised that Australia is ahead of the rest of the world in the time zone (only :-) - don't want to offend anyone or start a debate!! ) , so Monday deadline will mean it will be a weekend for the rest of the world. Just wanted to give everyone more time to submit their best, especially since I will be picking a second card too. Can't thank everyone enough for the submissions. P.S - Not keen on photos on the card.

Industry/Entity Type

Business

Contact Information for Business Card

Dr. Orin Halvey M.B.B.S., F.N.G.F.H.O
Family General Practitioner
Address, timings, phone and fax number on the back.

Requirements
Must have
• Timings
Mon 7 am - 7 pm
Tues 7 am - 12 pm
Wed 7 am - 10 pm
Thurs 7 am - 12 pm
Fri 7 am - 8 pm
Sat 8 am - 10 pm
Sun - Off

```html
<!DOCTYPE html>
<html lang="en">
<head>
<meta charset="utf-8">
<title>Dr. Orin Halvey – Business Card</title>
<link rel="stylesheet" href="https://fonts.googleapis.com/css2?family=Crimson+Text:ital,wght@0,400;0,600;0,700;1,400&family=Open+Sans:wght@700&display=swap">
<style>
  :root {
    --backdrop: #e9e6e1;
    --card-navy: #244a63;
    --card-edge: #1b384b;
    --ink-light: #ffffff;
    --stripe: #dfe6ea;
  }
  * { margin: 0; padding: 0; box-sizing: border-box; }
  html, body {
    width: 1200px; height: 396px; overflow: hidden;
    background: var(--backdrop);
  }
  .canvas { position: relative; width: 1200px; height: 396px; }

  .card {
    position: absolute; top: 48px; width: 546px; height: 312px;
    background: var(--card-navy); color: var(--ink-light);
  }
  .card--front { left: 43px; }
  .card--back { left: 622px; border: 1px solid var(--card-edge); }

  .stripe {
    position: absolute; left: 0; right: 0; height: 3px;
    background: var(--stripe);
  }
  .card--front .stripe--a { top: 4px; }
  .card--front .stripe--b { top: 12px; }
  .card--front .stripe--c { bottom: 14px; }
  .card--front .stripe--d { bottom: 5px; }
  .card--back .stripe--a { top: 198px; }
  .card--back .stripe--b { top: 207px; }

  .doctor-name {
    position: absolute; left: 69px; top: 94px;
    font-family: "Crimson Text", serif; font-style: italic; font-weight: 400;
    font-size: 38px; line-height: 1;
  }
  .credentials {
    position: absolute; left: 0; width: 404px; top: 157px; text-align: center;
    font-family: "Crimson Text", serif; font-style: italic; font-size: 12px; letter-spacing: 0.3px;
  }
  .role {
    position: absolute; left: 0; width: 404px; top: 205px; text-align: center;
    font-family: "Crimson Text", serif; font-style: italic; font-size: 18px;
  }
  .guild-mark {
    position: absolute; left: 382px; top: 112px; width: 132px;
    display: flex; flex-direction: column; align-items: center; gap: 8px;
  }
  .guild-mark__dot { width: 22px; height: 22px; border-radius: 50%; border: 2px solid var(--ink-light); }
  .guild-mark__name {
    font-family: "Crimson Text", serif; font-weight: 600; font-size: 15px;
    line-height: 1.15; text-align: center; color: var(--ink-light);
  }

  .hours-title {
    position: absolute; left: 0; right: 0; top: 29px; text-align: center;
    font-family: "Crimson Text", serif; font-weight: 600; font-size: 16px; letter-spacing: 0.3px;
  }
  .hours-table {
    position: absolute; left: 185px; top: 62px; border-collapse: collapse;
  }
  .hours-table td { height: 15.6px; line-height: 15.6px; padding: 0; vertical-align: middle; }
  .hours-table .day {
    width: 85px; font-family: "Crimson Text", serif; font-weight: 700; font-size: 13.5px;
  }
  .hours-table .sep { width: 15px; font-family: "Open Sans", sans-serif; font-weight: 700; font-size: 11px; }
  .hours-table .time { font-family: "Open Sans", sans-serif; font-weight: 700; font-size: 11px; white-space: pre; }

  .address {
    position: absolute; left: 0; right: 0; top: 225px; text-align: center;
    font-family: "Crimson Text", serif; font-weight: 600; font-size: 17.5px; line-height: 21px;
  }
  .contact-line {
    position: absolute; left: 0; right: 0; top: 278px; text-align: center;
    font-family: "Open Sans", sans-serif; font-weight: 700; font-size: 11px;
  }
</style>
</head>
<body>
<main class="canvas">
  <section class="card card--front" aria-label="Card front">
    <span class="stripe stripe--a"></span>
    <span class="stripe stripe--b"></span>
    <h1 class="doctor-name">Dr. Orin Halvey</h1>
    <p class="credentials">M.B.B.S., F.N.G.F.H.O</p>
    <p class="role">Family General Practitioner</p>
    <div class="guild-mark">
      <span class="guild-mark__dot"></span>
      <span class="guild-mark__name">Noble Guild of Family Healers Oceania</span>
    </div>
    <span class="stripe stripe--c"></span>
    <span class="stripe stripe--d"></span>
  </section>

  <section class="card card--back" aria-label="Card back">
    <h2 class="hours-title">Working Hours</h2>
    <table class="hours-table">
      <tr><td class="day">Monday</td><td class="sep">:</td><td class="time">7 AM -  7 PM</td></tr>
      <tr><td class="day">Tuesday</td><td class="sep">:</td><td class="time">7 AM - 12 PM</td></tr>
      <tr><td class="day">Wednesday</td><td class="sep">:</td><td class="time">7 AM - 10 PM</td></tr>
      <tr><td class="day">Thursday</td><td class="sep">:</td><td class="time">7 AM - 12 PM</td></tr>
      <tr><td class="day">Friday</td><td class="sep">:</td><td class="time">7 AM -  8 PM</td></tr>
      <tr><td class="day">Saturday</td><td class="sep">:</td><td class="time">8 AM - 10 PM</td></tr>
      <tr><td class="day">Sunday</td><td class="sep">:</td><td class="time">OFF</td></tr>
    </table>
    <span class="stripe stripe--a"></span>
    <span class="stripe stripe--b"></span>
    <p class="address">Lower Deck, Linden Arcade, Harrowgate Plaza Centre,<br>Brindle Vale, Nsw 2187</p>
    <p class="contact-line">P : 02 7314 5510 &nbsp;|&nbsp; F : 02 7314 5522</p>
  </section>
</main>
</body>
</html>
```